DuePath.com website design

We are a collection agency that collects debt from past residents of apartments on behalf of Property Management Companies. We are want to design a 3 page website with - Home - How it Works - Schedule Demo. We'd like a sketch of a skyline showing high rise apartment buildings, houses, shops, etc. We would like for there to be some animation, possibly clouds and the sun slowly moving. Maybe kids playing ball or catch or something like that. Bird flying and landing. An electric car charging (to indicate we are modern). We are looking for a friendly community vibe. The site will also need a button "Property Managers Login". When some comes to the site we would like a pop up that says "Property Managers Click Here/Past Residents Click Here" with a different icon for each that relates to the description. I've included a link to a test site we had designed so feel free to use some of the copy from it. We just aren't happy with the design. On the Home page our tag line should be "Get more payments, faster, from past residents!" and "Digital First, NOT Digital Only". All without transaction fees, we don't get paid unless we get you paid first!
Additional selling points:

24 hour virtual agent and virtual telephone agent so we don't miss any opportunities to GET YOUR MONEY!

Old school collection strategies meet cutting edge technology to create effective work flow algorithms to put the best debt collectors on your accounts with data driven intelligence to determine the best way to get paid.

No Subscription Fees
No Payment Processing Fees
No Software Fees
No Mail, Email or TXT Fees

Inquire about our FIRST PARTY accounts receivable outsourcing. You may qualify for free post move out A/R processing and AI payment negotiator for the low hanging fruit. Don't pay full collection commission when there wasn't a full collection attempt!

For the How it Works page - See the page from our previous design. I will include the link below. Please come up with your own version of this but you can use the copy from this page.

The schedule demo page will be a form that will feed to our CRM that will include:
Name
Email
Company
Title
Phone Number
Number of Units
Tell us how we can help you: (a box for them provide details)

Also include our phone number at the bottom with something like

Here is a link to our previous design test site:
https://brookpreview.net/duepath-new/
I've attached an image of the back end so you can get an idea of the colors we need, I've also included our logo. For the most part we would like most of the site to match the blue colors from our logo, but we do need to incorporate some of the yellow in the images I've attached. Possibly make the buttons on the site the yellow color? Make the sun Match the yellow? I'll leave it up to you.

```html
<!DOCTYPE html>
<html lang="en">
<head>
<meta charset="utf-8">
<title>DuePath – Home</title>
<link rel="stylesheet" href="https://fonts.googleapis.com/css2?family=Oswald:wght@400;500&family=Roboto:wght@400;500&family=Montserrat:wght@600&display=swap">
<style>
:root{
  --backdrop:#d8d8d8;
  --teal:#1fb8cb;
  --teal-dark:#17a6b8;
  --navy:#0c3b74;
  --ink:#222;
  --peach:#fcd89b;
  --peach-light:#fde3a3;
  --gold:#f9d48b;
  --field-line:#d6d6d6;
  --white:#fff;
}
*{box-sizing:border-box;margin:0;padding:0}
html,body{width:1185px;height:1200px;overflow:hidden;background:var(--backdrop)}
body{font-family:'Roboto',Arial,sans-serif;color:var(--ink)}
.stage{position:absolute;left:0;top:0;width:1908px;height:1932px;transform:scale(.62107);transform-origin:0 0}
.page{position:absolute;top:86px;width:829px;height:1750px;background:var(--white);overflow:hidden;box-shadow:0 0 6px rgba(0,0,0,.06)}
.page--home{left:89px}
.page--login{left:990px}

/* header */
.brand{position:absolute;left:77px;top:12px;display:flex;align-items:center;gap:8px}
.brand__mark{width:26px;height:26px;border:3px solid var(--teal);border-radius:6px}
.brand__name{font-family:'Oswald',sans-serif;font-size:25px;font-weight:400;color:var(--teal)}
.nav{position:absolute;top:19px;left:310px;display:flex;gap:20px;font-size:10px;font-weight:500;text-transform:uppercase}
.nav a{color:var(--ink);text-decoration:none;padding-bottom:5px}
.nav a.is-current{color:var(--teal);border-bottom:1.5px solid var(--teal)}
.btn{display:inline-flex;align-items:center;justify-content:center;background:var(--teal);color:var(--white);border-radius:20px;font-size:10px;font-weight:500;text-transform:uppercase;border:0}
.btn--login{position:absolute;left:577px;top:10px;width:174px;height:31px}

/* hero */
.hero__text{position:absolute;left:76px;top:174px;font-family:'Oswald',sans-serif}
.hero__lead{font-size:24px;line-height:30px;color:var(--ink);font-weight:400}
.hero__tag{font-size:26px;color:var(--navy);margin-top:12px;font-weight:400}
.hero__dots{position:absolute;left:76px;top:357px;display:flex;gap:6px}
.hero__dots span{width:8px;height:8px;border-radius:50%;background:#cfcfcf}
.hero__dots span:first-child{background:var(--teal)}
.hero__art{position:absolute;left:378px;top:88px;width:451px;height:296px;border-radius:6px;
  background:linear-gradient(180deg,#fff 0%,#e9f4f7 25%,#7fcde0 50%,#f6b53c 72%,#f08b2e 85%,#fff 100%)}

/* fees band */
.fees{position:absolute;left:0;top:409px;width:829px;height:305px;background:var(--teal);color:var(--white);text-align:center}
.section-title{font-family:'Oswald',sans-serif;font-weight:400;font-size:27px}
.section-rule{width:48px;height:2px;margin:12px auto 0}
.fees .section-title{margin-top:58px}
.fees .section-rule{background:var(--white)}
.fees__list{position:absolute;top:134px;left:0;width:829px}
.fee{position:absolute;width:140px;text-align:center;font-size:12px;font-weight:500;line-height:17px}
.fee__icon{width:66px;height:62px;margin:0 auto 12px;border-radius:8px;background:var(--peach);border:3px solid var(--white);display:flex;align-items:center;justify-content:center}

/* agent band */
.agent{position:absolute;left:0;top:714px;width:829px;height:237px;background:var(--navy)}
.agent__art{position:absolute;left:-60px;top:0;width:357px;height:237px;border-radius:0 50% 50% 0/0 50% 50% 0;
  background:radial-gradient(circle at 55% 45%,#d8ecf6 0%,#a8d46a 45%,#6aa53a 75%,#8b8f97 100%)}
.agent__copy{position:absolute;left:361px;top:72px;font-family:'Oswald',sans-serif;font-size:25px;line-height:30px;color:var(--white);font-weight:400}
.agent__copy em{font-style:normal;color:var(--gold)}

/* contact form */
.contact{position:absolute;left:0;top:951px;width:829px;text-align:center}
.contact .section-title{margin-top:62px;font-size:29px;color:var(--ink)}
.contact .section-rule{background:var(--teal);margin-top:9px}
.field{position:absolute;height:40px;border:1px solid var(--field-line);border-radius:20px;font-size:10px;color:#555;text-align:left;padding:0 19px;display:flex;align-items:center}
.field--area{height:136px;align-items:flex-start;padding-top:16px;border-radius:24px}
.btn--submit{position:absolute;left:357px;top:445px;width:115px;height:31px}

/* footer */
.footer{position:absolute;left:0;top:1497px;width:829px;height:253px;background:var(--navy);color:var(--white)}
.footer h4{font-family:'Montserrat',sans-serif;font-weight:600;font-size:15px;position:absolute;top:61px}
.footer ul{list-style:none;position:absolute;top:95px;font-size:10.5px;line-height:19.5px}
.footer__divider{position:absolute;top:65px;width:1px;height:102px;background:rgba(255,255,255,.45)}
.contact-list li{display:flex;gap:12px;align-items:flex-start}
.contact-list svg{flex:none;margin-top:5px}
.socials{position:absolute;top:92px;left:621px;display:flex;gap:6px}
.socials span{width:26px;height:26px;border:1px solid var(--white);border-radius:50%}
.copyright{position:absolute;top:218px;left:0;width:829px;text-align:center;font-size:10px}

/* login modal */
.dim{position:absolute;inset:0;background:rgba(20,20,20,.45)}
.modal{position:absolute;left:143px;top:180px;width:542px;height:295px;background:var(--white);border-radius:30px;text-align:center}
.modal__title{font-family:'Oswald',sans-serif;font-weight:400;font-size:32px;margin-top:32px;color:var(--ink)}
.modal__close{position:absolute;right:22px;top:18px;font-size:20px;font-weight:500;color:#111}
.choice{position:absolute;top:103px;width:141px;height:141px;border-radius:10px;background:var(--peach-light);font-family:'Oswald',sans-serif;font-size:12px;line-height:18px;color:var(--ink)}
.choice__icon{width:50px;height:50px;border-radius:50%;background:var(--white);margin:27px auto 12px;display:flex;align-items:center;justify-content:center}
</style>
</head>
<body>
<div class="stage">

  <!-- Home page -->
  <section class="page page--home">
    <header>
      <div class="brand"><span class="brand__mark"></span><span class="brand__name">DuePath</span></div>
      <nav class="nav"><a class="is-current" href="#">Home</a><a href="#">How it works</a><a href="#">Schedule demo</a></nav>
      <a class="btn btn--login">Property managers login</a>
    </header>
    <div class="hero__text">
      <h1 class="hero__lead">Get more payments, faster,<br>from past residents!</h1>
      <p class="hero__tag">Digital First, NOT Digital Only</p>
    </div>
    <div class="hero__dots"><span></span><span></span><span></span></div>
    <div class="hero__art" role="img" aria-label="Colourful city skyline illustration with apartment towers, houses, a car, cyclists and people walking"></div>

    <section class="fees">
      <h2 class="section-title">Best Way to Get Paid</h2>
      <div class="section-rule"></div>
      <div class="fees__list">
        <div class="fee" style="left:91px"><div class="fee__icon"><svg width="36" height="36" viewBox="0 0 36 36" fill="none" stroke="#3a3a3a" stroke-width="2"><circle cx="18" cy="18" r="14"/><line x1="8" y1="28" x2="28" y2="8"/></svg></div>No Subscription Fees</div>
        <div class="fee" style="left:260px"><div class="fee__icon"><svg width="36" height="36" viewBox="0 0 36 36" fill="none" stroke="#3a3a3a" stroke-width="2"><rect x="9" y="6" width="18" height="24" rx="2"/><line x1="13" y1="14" x2="23" y2="14"/><line x1="13" y1="20" x2="23" y2="20"/></svg></div>No Payment<br>Processing Fees</div>
        <div class="fee" style="left:428px"><div class="fee__icon"><svg width="36" height="36" viewBox="0 0 36 36" fill="none" stroke="#3a3a3a" stroke-width="2"><circle cx="18" cy="18" r="14"/><circle cx="18" cy="18" r="9"/><line x1="8" y1="28" x2="28" y2="8"/></svg></div>No Software Fees</div>
        <div class="fee" style="left:597px"><div class="fee__icon"><svg width="36" height="36" viewBox="0 0 36 36" fill="none" stroke="#3a3a3a" stroke-width="2"><rect x="7" y="6" width="22" height="6"/><path d="M10 12v18l4-2 4 2 4-2 4 2V12"/></svg></div>No Mail, Email or<br>TXT Fees</div>
      </div>
    </section>

    <section class="agent">
      <div class="agent__art" role="img" aria-label="Isometric illustration of green high-rise apartment buildings beside a road"></div>
      <p class="agent__copy">24 hour virtual agent and virtual<br>telephone agent so we don't miss any<br>opportunities to <em>GET YOUR MONEY</em></p>
    </section>

    <section class="contact">
      <h2 class="section-title">Get in Touch</h2>
      <div class="section-rule"></div>
      <div class="field" style="left:138px;top:134px;width:268px">Name</div>
      <div class="field" style="left:422px;top:134px;width:268px">Email</div>
      <div class="field" style="left:138px;top:187px;width:268px">Company</div>
      <div class="field" style="left:422px;top:187px;width:268px">Title</div>
      <div class="field" style="left:138px;top:239px;width:268px">Phone Number</div>
      <div class="field" style="left:422px;top:239px;width:268px">Number of Units</div>
      <div class="field field--area" style="left:140px;top:291px;width:550px">Tell us how we can help you:</div>
      <a class="btn btn--submit">Submit now</a>
    </section>

    <footer class="footer">
      <h4 style="left:96px">Links</h4>
      <ul style="left:96px"><li>Home</li><li>Services</li><li>Testimonials</li><li>Contact</li></ul>
      <div class="footer__divider" style="left:232px"></div>
      <h4 style="left:319px">Contact us</h4>
      <ul class="contact-list" style="left:319px">
        <li><svg width="8" height="10" viewBox="0 0 8 10"><path d="M4 0a4 4 0 0 1 4 4c0 3-4 6-4 6S0 7 0 4a4 4 0 0 1 4-4z" fill="#fff"/><circle cx="4" cy="4" r="1.4" fill="#0c3b74"/></svg><span>123,Lorem ipsum dolor sit amet,<br>consectetur</span></li>
        <li><svg width="9" height="9" viewBox="0 0 10 10"><path d="M2 0l2 2.5-1.2 1.5a6 6 0 0 0 3.2 3.2L7.5 6 10 8l-1.5 2C4 10 0 6 0 1.5z" fill="#fff"/></svg><span>+1 888 888 8888</span></li>
        <li><svg width="10" height="8" viewBox="0 0 10 8"><rect width="10" height="8" rx="1" fill="#fff"/><path d="M0 1l5 3.5L10 1" stroke="#0c3b74" fill="none"/></svg><span>info@companyname.com</span></li>
      </ul>
      <div class="footer__divider" style="left:565px"></div>
      <h4 style="left:651px">Follow us</h4>
      <div class="socials"><span></span><span></span><span></span><span></span></div>
      <p class="copyright">© Copyrights.2022.The Company Name.All Rights Reserved</p>
    </footer>
  </section>

  <!-- Home page with login chooser open -->
  <section class="page page--login">
    <header>
      <div class="brand"><span class="brand__mark"></span><span class="brand__name">DuePath</span></div>
      <nav class="nav"><a class="is-current" href="#">Home</a><a href="#">How it works</a><a href="#">Schedule demo</a></nav>
      <a class="btn btn--login">Property managers login</a>
    </header>
    <div class="hero__text">
      <h1 class="hero__lead">Get more payments, faster,<br>from past residents!</h1>
      <p class="hero__tag">Digital First, NOT Digital Only</p>
    </div>
    <div class="hero__dots"><span></span><span></span><span></span></div>
    <div class="hero__art" role="img" aria-label="Colourful city skyline illustration with apartment towers, houses, a car, cyclists and people walking"></div>

    <section class="fees">
      <h2 class="section-title">Best Way to Get Paid</h2>
      <div class="section-rule"></div>
      <div class="fees__list">
        <div class="fee" style="left:91px"><div class="fee__icon"><svg width="36" height="36" viewBox="0 0 36 36" fill="none" stroke="#3a3a3a" stroke-width="2"><circle cx="18" cy="18" r="14"/><line x1="8" y1="28" x2="28" y2="8"/></svg></div>No Subscription Fees</div>
        <div class="fee" style="left:260px"><div class="fee__icon"><svg width="36" height="36" viewBox="0 0 36 36" fill="none" stroke="#3a3a3a" stroke-width="2"><rect x="9" y="6" width="18" height="24" rx="2"/><line x1="13" y1="14" x2="23" y2="14"/><line x1="13" y1="20" x2="23" y2="20"/></svg></div>No Payment<br>Processing Fees</div>
        <div class="fee" style="left:428px"><div class="fee__icon"><svg width="36" height="36" viewBox="0 0 36 36" fill="none" stroke="#3a3a3a" stroke-width="2"><circle cx="18" cy="18" r="14"/><circle cx="18" cy="18" r="9"/><line x1="8" y1="28" x2="28" y2="8"/></svg></div>No Software Fees</div>
        <div class="fee" style="left:597px"><div class="fee__icon"><svg width="36" height="36" viewBox="0 0 36 36" fill="none" stroke="#3a3a3a" stroke-width="2"><rect x="7" y="6" width="22" height="6"/><path d="M10 12v18l4-2 4 2 4-2 4 2V12"/></svg></div>No Mail, Email or<br>TXT Fees</div>
      </div>
    </section>

    <section class="agent">
      <div class="agent__art" role="img" aria-label="Isometric illustration of green high-rise apartment buildings beside a road"></div>
      <p class="agent__copy">24 hour virtual agent and virtual<br>telephone agent so we don't miss any<br>opportunities to <em>GET YOUR MONEY</em></p>
    </section>

    <section class="contact">
      <h2 class="section-title">Get in Touch</h2>
      <div class="section-rule"></div>
      <div class="field" style="left:138px;top:134px;width:268px">Name</div>
      <div class="field" style="left:422px;top:134px;width:268px">Email</div>
      <div class="field" style="left:138px;top:187px;width:268px">Company</div>
      <div class="field" style="left:422px;top:187px;width:268px">Title</div>
      <div class="field" style="left:138px;top:239px;width:268px">Phone Number</div>
      <div class="field" style="left:422px;top:239px;width:268px">Number of Units</div>
      <div class="field field--area" style="left:140px;top:291px;width:550px">Tell us how we can help you:</div>
      <a class="btn btn--submit">Submit now</a>
    </section>

    <footer class="footer">
      <h4 style="left:96px">Links</h4>
      <ul style="left:96px"><li>Home</li><li>Services</li><li>Testimonials</li><li>Contact</li></ul>
      <div class="footer__divider" style="left:232px"></div>
      <h4 style="left:319px">Contact us</h4>
      <ul class="contact-list" style="left:319px">
        <li><svg width="8" height="10" viewBox="0 0 8 10"><path d="M4 0a4 4 0 0 1 4 4c0 3-4 6-4 6S0 7 0 4a4 4 0 0 1 4-4z" fill="#fff"/><circle cx="4" cy="4" r="1.4" fill="#0c3b74"/></svg><span>123,Lorem ipsum dolor sit amet,<br>consectetur</span></li>
        <li><svg width="9" height="9" viewBox="0 0 10 10"><path d="M2 0l2 2.5-1.2 1.5a6 6 0 0 0 3.2 3.2L7.5 6 10 8l-1.5 2C4 10 0 6 0 1.5z" fill="#fff"/></svg><span>+1 888 888 8888</span></li>
        <li><svg width="10" height="8" viewBox="0 0 10 8"><rect width="10" height="8" rx="1" fill="#fff"/><path d="M0 1l5 3.5L10 1" stroke="#0c3b74" fill="none"/></svg><span>info@companyname.com</span></li>
      </ul>
      <div class="footer__divider" style="left:565px"></div>
      <h4 style="left:651px">Follow us</h4>
      <div class="socials"><span></span><span></span><span></span><span></span></div>
      <p class="copyright">© Copyrights.2022.The Company Name.All Rights Reserved</p>
    </footer>

    <div class="dim"></div>
    <div class="modal" role="dialog" aria-label="Login With">
      <span class="modal__close">✕</span>
      <h2 class="modal__title">Login With</h2>
      <a class="choice" style="left:113px">
        <div class="choice__icon"><svg width="28" height="28" viewBox="0 0 28 28"><path d="M14 3L2 13h3v12h18V13h3z" fill="#0c3b74"/><circle cx="14" cy="17" r="4.5" fill="#fff"/><circle cx="14" cy="17" r="2" fill="#0c3b74"/></svg></div>
        Property Managers<br>Click Here
      </a>
      <a class="choice" style="left:288px">
        <div class="choice__icon"><svg width="28" height="28" viewBox="0 0 28 28"><path d="M14 3L2 13h3v12h18V13h3z" fill="#0c3b74"/><circle cx="14" cy="15" r="3" fill="#fff"/><path d="M8.5 24a5.5 5 0 0 1 11 0z" fill="#fff"/></svg></div>
        Past Residents<br>Click Here
      </a>
    </div>
  </section>

</div>
</body>
</html>
```